Brell Stone Company Business Cards

Front and Back Business Card - logo and text setup - cool design. I need workable photoshop or illustrator files so I can setup each employee card with design that is created
Updates

Hi everyone, thank you for the great entries. Please no more white and blue cards - there are so many already - black and silver only now please. thanks!

Target Market(s)

Construction Industry - Facility Managers

Industry/Entity Type

Construction

Contact Information for Business Card

I really like contemporary simplistic looks - clean neat....not opposed to seeing some black backrounds

Requirements
Must have
• Logo/website address with design on front only - www.brellstone-example.com (logo attached)
• Back:
• Name/Title/Company Address/Phone/email address
Nice to have
• Cool design
Should not have
• Nothing gimmicky like Fire or Water - since we are a Fire Protection company - it has all been done

```html
<!DOCTYPE html>
<html lang="en">
<head>
<meta charset="utf-8">
<title>Brell Stone Company Business Cards</title>
<link href="https://fonts.googleapis.com/css2?family=Lato:wght@400;700;900&display=swap" rel="stylesheet">
<style>
  :root {
    --backdrop: #3b3b3b;
    --card-dark: #2b2a2c;
    --card-glow: #58575a;
    --card-light: #ecedee;
    --navy: #1f3a6e;
    --red: #df4a33;
    --grey-text: #5d5f63;
    --rule: #8b8d90;
    --silver: #e6e6e6;
  }
  * { margin: 0; padding: 0; box-sizing: border-box; }
  html, body { width: 1200px; height: 829px; overflow: hidden; }
  body {
    background: var(--backdrop);
    font-family: "Lato", sans-serif;
    position: relative;
  }
  .card {
    position: absolute;
    top: 282px;
    width: 485px;
    height: 277px;
    box-shadow: 0 6px 14px rgba(0,0,0,.45);
  }
  .card-front {
    left: 82px;
    background: radial-gradient(ellipse 220px 170px at 290px 150px, var(--card-glow), var(--card-dark) 100%);
  }
  .card-back {
    left: 628px;
    background: var(--card-light);
  }
  .front-name {
    position: absolute;
    left: 0; right: 0;
    top: 108px;
    text-align: center;
    font-weight: 900;
    font-size: 46px;
    letter-spacing: -1px;
    color: var(--silver);
  }
  .front-web {
    position: absolute;
    left: 0; right: 0;
    top: 232px;
    text-align: center;
    font-size: 11px;
    letter-spacing: 1.4px;
    color: #d8d8d8;
  }
  .front-web b { font-weight: 700; }
  .back-name {
    position: absolute;
    right: 39px;
    top: 36px;
    font-weight: 900;
    font-size: 34px;
    letter-spacing: -0.5px;
    color: var(--navy);
  }
  .person {
    position: absolute;
    left: 38px;
    top: 152px;
  }
  .person-name { font-weight: 700; font-size: 15px; color: var(--navy); line-height: 18px; }
  .person-name span { color: var(--red); }
  .person-title { font-size: 11.5px; color: var(--grey-text); line-height: 14px; }
  .rule {
    position: absolute;
    left: 38px; right: 39px;
    top: 199px;
    height: 1px;
    background: var(--rule);
  }
  .contact {
    position: absolute;
    left: 38px;
    top: 214px;
    font-size: 11.5px;
    line-height: 15px;
    color: var(--grey-text);
  }
  .contact-row { display: flex; align-items: center; gap: 5px; }
  .contact-row svg { width: 9px; height: 9px; fill: var(--navy); }
  .address {
    position: absolute;
    right: 39px;
    top: 214px;
    text-align: right;
    font-size: 11.5px;
    line-height: 15px;
    color: var(--grey-text);
  }
</style>
</head>
<body>
  <section class="card card-front">
    <div class="front-name">Brell Stone</div>
    <div class="front-web">www.<b>brellstone-example</b>.com</div>
  </section>

  <section class="card card-back">
    <div class="back-name">Brell Stone</div>
    <div class="person">
      <div class="person-name">Daniel <span>Marsh</span></div>
      <div class="person-title">Managing Director</div>
    </div>
    <div class="rule"></div>
    <div class="contact">
      <div class="contact-row">
        <svg viewBox="0 0 10 10"><path d="M2 0.5 L3.8 2.6 L2.9 3.7 Q4 6 6.3 7.1 L7.4 6.2 L9.5 8 L8.3 9.5 Q4.5 9.5 0.5 1.7 Z"/></svg>
        <span>300.555.0142</span>
      </div>
      <div class="contact-row">
        <svg viewBox="0 0 10 10"><path d="M0.5 2 H9.5 V8 H0.5 Z M1.5 3 V7 H8.5 V3 L5 5.5 Z" fill-rule="evenodd"/></svg>
        <span>info@brellstone-example.com</span>
      </div>
    </div>
    <div class="address">
      <div>Co. Street, Suite, Building</div>
      <div>City/State, Zip Code</div>
    </div>
  </section>
</body>
</html>
```